Business Card Design for Vintage Jazz

I am a vintage jazz band leader in New York City. My groups play the music of the 1920s, 1930s and 1940s. My website is morvalquist.com for more info on what I do.

I am looking for a two sided business card design that has the look and feel of a really nice business card from the 1930s. I need to convey with the design that my work has that vintage kind of class and style, but also conveys that we are fun and entertaining.

Most importantly it should make a bold staement. If Hal Denbrook had a card, what would it have looked like? I want a card that I feel confident will make an impact and will let people know that my work is te the top that NYC has to offer in vintage jazz..

Note that I have only decided to avoid the "committed payment" option as I have not used this service before. Assuming that I get quality work I will select a design from those presented.

Target Market(s)

people who want to hire my band for events, media, and new fans of the band

Industry/Entity Type

Performing Art

Contact Information for Business Card

Definitely a matte finish, possibly a sort of old style of paper with that brown tint? definitely a thick card.

Requirements
Must have
• FRONT
• My name: Tobin Vashley
• What I do: Bandleader, Guitarist, Vocalist, Songwriter
• Contact Details: morvalquist.com tobin@morvalquist.com 646-555-0148
• BACK
• My Social Media Links:
• facebook.morvalquist.com
• twitter, instagram, linkedin: morvalquist
• I'm also including a photo image I would like to use. The photo's background is not needed, and to be honest isn't really desireable. Just looking to use the image of me.
Nice to have
• I'm attaching which could be used as is, omitted from the card, or altered maybe with text going around the outside of the circle or in some other way. It may need some clean up to the edges of the lettering as we only use it for the website thumbnail.
• If there's space I'd like to include the text "join our mailing list for a free song download: freesong.morvalquist.com" If not perhaps just "Download a Free Song at: freesong.morvalquist.com - something to this end.
Should not have
• anything cartoony. Don't think retro 90s's vision of the swing era, think actual swing era!
• anything modern. Got to look old school
• Try to avoid dark backgrounds. Since we often play in bars and clubs where it is dar, a d
• avoid script fonts.

```html
<!DOCTYPE html>
<html lang="en">
<head>
<meta charset="utf-8">
<title>Tobin Vashley – Business Card</title>
<link rel="stylesheet" href="https://fonts.googleapis.com/css2?family=Open+Sans:ital,wght@0,400;0,600;1,400;1,600&display=swap">
<style>
  :root {
    --backdrop: #2e2e2e;
    --card: #ffffff;
    --ink: #111111;
    --ink-soft: #555555;
    --rule: #cfcfcf;
    --photo-light: #e6e6e6;
    --photo-dark: #3a3a3a;
  }
  * { margin: 0; padding: 0; box-sizing: border-box; }
  html, body {
    width: 1200px; height: 886px; overflow: hidden;
    background: var(--backdrop);
    font-family: "Open Sans", sans-serif;
  }
  .canvas { position: relative; width: 1200px; height: 886px; }
  .card {
    position: absolute; width: 565px; height: 323px;
    background: var(--card); border-radius: 16px; overflow: hidden;
  }
  .card--front { left: 315px; top: 102px; }
  .card--back  { left: 312px; top: 460px; }

  .brand { position: absolute; display: flex; align-items: center; gap: 10px; }
  .brand__dot { border-radius: 50%; background: var(--ink); flex: none; }
  .brand__name { color: var(--ink); font-weight: 600; }
  .card--front .brand { left: 40px; top: 146px; }
  .card--front .brand__dot { width: 34px; height: 34px; }
  .card--front .brand__name { font-size: 21px; }
  .card--back .brand { left: 28px; top: 60px; }
  .card--back .brand__dot { width: 30px; height: 30px; }
  .card--back .brand__name { font-size: 19px; }

  .divider {
    position: absolute; left: 260px; top: 84px; width: 1px; height: 160px;
    background: var(--rule);
  }
  .identity { position: absolute; left: 294px; top: 86px; }
  .identity__name { font-size: 19.5px; font-weight: 600; color: var(--ink); line-height: 1.2; }
  .identity__role { font-size: 15.5px; color: var(--ink-soft); line-height: 1.35; }

  .contacts { position: absolute; left: 296px; top: 170px; list-style: none; }
  .contacts li {
    display: flex; align-items: center; gap: 8px;
    font-size: 15px; color: var(--ink-soft); height: 21.5px;
  }
  .contacts svg { width: 14px; height: 14px; flex: none; }

  .socials { position: absolute; left: 30px; top: 151px; list-style: none; }
  .socials li {
    display: flex; align-items: center; gap: 10px;
    font-size: 15.5px; color: var(--ink-soft); height: 26px;
  }
  .socials .social-dot { width: 20px; height: 20px; border-radius: 50%; background: var(--ink); flex: none; }

  .free-song { position: absolute; left: 29px; top: 262px; font-style: italic; font-size: 15px; color: var(--ink-soft); line-height: 1.3; }
  .free-song strong { font-weight: 600; color: #333; }

  .portrait {
    position: absolute; left: 262px; top: 12px; width: 300px; height: 311px;
    background: linear-gradient(180deg, var(--photo-light) 0%, #bdbdbd 35%, var(--photo-dark) 100%);
    border-radius: 40% 40% 0 0 / 20% 20% 0 0;
  }
</style>
</head>
<body>
<main class="canvas">

  <section class="card card--front" aria-label="Card front">
    <div class="brand"><span class="brand__dot"></span><span class="brand__name">Morvalquist</span></div>
    <div class="divider"></div>
    <div class="identity">
      <h1 class="identity__name">Tobin Vashley</h1>
      <p class="identity__role">Bandleader, Guitarist<br>Vocalist, Songwriter</p>
    </div>
    <ul class="contacts">
      <li>
        <svg viewBox="0 0 14 14" aria-hidden="true"><rect x="3.5" y="0.5" width="7" height="13" rx="1.2" fill="none" stroke="#111" stroke-width="1.4"/><rect x="5" y="2.2" width="4" height="8" fill="#111"/></svg>
        646-555-0148
      </li>
      <li>
        <svg viewBox="0 0 14 14" aria-hidden="true"><rect x="0.5" y="3" width="13" height="8.5" fill="#111"/><path d="M0.5 3 L7 8 L13.5 3" fill="none" stroke="#fff" stroke-width="1.1"/></svg>
        tobin@morvalquist.com
      </li>
      <li>
        <svg viewBox="0 0 14 14" aria-hidden="true"><circle cx="7" cy="7" r="6.3" fill="#111"/><ellipse cx="7" cy="7" rx="2.6" ry="6.3" fill="none" stroke="#fff" stroke-width="0.9"/><line x1="0.7" y1="7" x2="13.3" y2="7" stroke="#fff" stroke-width="0.9"/></svg>
        morvalquist.com
      </li>
    </ul>
  </section>

  <section class="card card--back" aria-label="Card back">
    <div class="brand"><span class="brand__dot"></span><span class="brand__name">Morvalquist</span></div>
    <ul class="socials">
      <li><span class="social-dot"></span>morvalquist.com</li>
      <li><span class="social-dot"></span>morvalquist</li>
      <li><span class="social-dot"></span>morvalquist</li>
      <li><span class="social-dot"></span>morvalquist</li>
    </ul>
    <p class="free-song">Download a Free Song at:<br><strong>freesong.morvalquist.com</strong></p>
    <div class="portrait" role="img" aria-label="Black-and-white photo of the bandleader in a striped-edge blazer and cravat, tipping a straw boater hat"></div>
  </section>

</main>
</body>
</html>
```